Belvascotravel.com web design project + logo design

Hi,

We are a Russian online tour operator - sunkettle.com

We are looking to tranmsfer our domain to belvascotravel.com. The website and logo need to be belvascoesque - we are not looking to change our functionality, but we need to make the website much more attracitve to clients, much more wild looking but at the same time remaining a professional travel company.

The main concept of the website should be innovative travel (as belvasco was an innovator). Alternatively, you could go down the artist route and go down the draw / design your own tour road.

On our website the customer is able to combine travel services (hotels, flights, Visa services, and soon chauffeur, car rental etc...) put it into their basket (the basket definitely has to look better than it is at the moment) and pay for it in one go by card.

We are also stressin our customer support with web chat, call centre etc... (call centre number at the top of the page)

We aim to provide an easy user experience, but we need to make it have some more style, so I will be waiting for what you guys can come up with.
Let me know if you have any questions - skype is: mrdolbarin

Industry/Entity Type

It Company

Requirements
Must have
• It is quite a simple task - to take the existing website sunkettle.com and belvascosize it to create belvascotravel.com, the functionality of the website will remain the same and there are not many pages in the website. Homepage, Checkout step1, Checkout step 2 (you can view both of these if you select a service) and the generic pages for T&C''s, Privacy policy etc...

IMPORTANT UPDATE

We are also looking at how the search results will look in the designs, (please do a search on our website for hotel / flight)

```html
<!DOCTYPE html>
<html lang="en">
<head>
<meta charset="utf-8">
<title>Belvasco Travel</title>
<link rel="stylesheet" href="https://fonts.googleapis.com/css2?family=Questrial&family=Open+Sans:wght@400;600&display=swap">
<style>
:root{
  --page-bg:#ececec;
  --sheet:#ffffff;
  --blue:#3a9ad9;
  --blue-dark:#2c86c6;
  --blue-title:#2f8ccc;
  --green:#5a9e3a;
  --green-dark:#468a2b;
  --text:#444444;
  --muted:#8a8a8a;
  --field-text:#7a7a7a;
  --card-bg:#f1f1f1;
  --footer:#3d3d3d;
  --footer-bottom:#333333;
  --footer-text:#9a9a9a;
  --footer-line:#4f4f4f;
}
*{margin:0;padding:0;box-sizing:border-box}
html,body{width:1125px;height:1200px;overflow:hidden;background:var(--page-bg)}
body{font-family:"Questrial",sans-serif;color:var(--text);position:relative}
.sheet{position:absolute;left:94px;top:0;width:937px;height:1200px;background:var(--sheet);box-shadow:0 0 6px rgba(0,0,0,.12)}
.abs{position:absolute}

/* header */
.brand{left:127px;top:40px;display:flex;align-items:center;gap:8px}
.brand-dot{width:26px;height:26px;border-radius:50%;background:var(--blue-dark)}
.brand-name{font-family:"Open Sans",sans-serif;font-weight:600;font-size:21px;color:var(--blue-dark)}
.support{left:698px;top:45px;display:flex;gap:8px;align-items:center}
.support-label{font-size:11px;color:var(--green);letter-spacing:.2px}
.support-phone{font-size:20px;color:#333;line-height:22px}
.lang{left:895px;top:45px;width:113px;height:35px;border:1px solid #d6d6d6;border-radius:2px;display:flex;align-items:center;padding-left:9px;gap:8px;font-family:"Open Sans",sans-serif;font-size:13px;color:#333}
.lang-caret{margin-left:6px;border-left:4px solid transparent;border-right:4px solid transparent;border-top:5px solid #333}

/* nav + hero */
.hero{left:103px;top:123px;width:919px;height:342px;overflow:hidden}
.hero-photo{position:absolute;inset:0;background:linear-gradient(180deg,#bcd6ea 0%,#e3edf4 30%,#5f7a52 40%,#6fc0c5 52%,#8fd2d0 75%,#a9dad6 100%)}
.nav{position:absolute;left:0;top:0;width:919px;height:41px;background:var(--blue);display:flex;font-family:"Open Sans",sans-serif;font-size:12px;color:#fff}
.nav a{color:#fff;text-decoration:none;line-height:41px;text-align:center;border-right:1px solid rgba(255,255,255,.25)}
.nav a:last-child{border-right:none}
.hero-curve{position:absolute;left:0;top:40px}
.hero-title{position:absolute;left:24px;top:284px;font-size:30px;color:#1e1e1e;letter-spacing:.3px}

/* search */
.search{left:103px;top:465px;width:919px;height:119px;background:var(--blue)}
.field{position:absolute;height:31px;background:#fff;font-family:"Open Sans",sans-serif;font-size:13px;color:var(--field-text);padding-left:14px;line-height:31px}
.field.select::after{content:"";position:absolute;right:9px;top:13px;border-left:5px solid transparent;border-right:5px solid transparent;border-top:6px solid var(--blue-dark)}
.checks{position:absolute;left:638px;top:67px;font-family:"Open Sans",sans-serif;font-size:11px;color:#fff;line-height:17px}
.check{display:flex;align-items:center;gap:5px}
.box{width:11px;height:11px;background:#fff;border:1px solid #bbb;display:inline-flex;align-items:center;justify-content:center}
.proceed{position:absolute;left:750px;top:66px;width:153px;height:32px;background:linear-gradient(#66ad43,var(--green-dark));color:#fff;font-family:"Open Sans",sans-serif;font-weight:600;font-size:14px;text-align:center;line-height:32px;box-shadow:0 2px 3px rgba(0,0,0,.2)}

/* welcome */
.world-map{left:120px;top:619px;width:229px;height:131px;background:radial-gradient(ellipse at center,#3f7fbf 0%,#5c93c9 55%,#e7eff7 80%,#ffffff 100%);border-radius:40%}
.welcome-title{left:382px;top:623px;font-size:26px;color:var(--blue-title)}
.welcome-text{left:382px;top:671px;width:620px;font-family:"Open Sans",sans-serif;font-size:12.5px;line-height:21.5px;color:var(--muted)}

/* services */
.section-title{left:125px;top:775px;font-family:"Open Sans",sans-serif;font-size:17px;color:#444}
.section-rule{left:240px;top:784px;width:762px;height:3px;border-top:1px solid #e2e2e2;border-bottom:1px solid #e2e2e2}
.card{position:absolute;top:811px;width:207px;height:183px;background:var(--card-bg)}
.card-photo{height:145px}
.card-label{text-align:center;font-family:"Open Sans",sans-serif;font-size:15px;color:#444;line-height:38px}
.card.active{border-bottom:3px solid var(--green)}
.card.active .card-label{line-height:40px}

/* footer */
.footer{left:103px;top:1037px;width:919px;height:125px;background:var(--footer);font-family:"Open Sans",sans-serif;font-size:11px;color:var(--footer-text)}
.footer-notch{position:absolute;left:449px;top:0;border-left:9px solid transparent;border-right:9px solid transparent;border-top:9px solid #fff}
.footer-links{position:absolute;left:19px;top:37px;display:flex;gap:36px;color:#7c7c7c}
.footer-rule{position:absolute;top:59px;height:1px;background:var(--footer-line)}
.footer-info{position:absolute;top:73px;display:flex;align-items:center;gap:8px}
.stay{position:absolute;left:693px;top:33px;font-size:10.5px;color:#a5a5a5}
.social{position:absolute;top:73px;width:15px;height:15px;border-radius:50%;background:#6c6c6c}
.footer-bottom{left:103px;top:1162px;width:919px;height:38px;background:var(--footer-bottom);font-family:"Open Sans",sans-serif;font-size:11px;color:#8d8d8d;display:flex;align-items:center;padding-left:19px}
.footer-bottom span{padding:0 15px;border-left:1px solid #555}
.footer-bottom span:first-child{padding-left:0;border-left:none}
</style>
</head>
<body>
<div class="sheet"></div>

<header>
  <div class="abs brand"><span class="brand-dot"></span><span class="brand-name">belvascotravel.com</span></div>
  <div class="abs support">
    <svg width="38" height="38" viewBox="0 0 38 38" aria-hidden="true">
      <path d="M7 22 V17 a12 12 0 0 1 24 0 V22" fill="none" stroke="#333" stroke-width="3"/>
      <rect x="4" y="19" width="7" height="11" rx="2" fill="#333"/>
      <rect x="27" y="19" width="7" height="11" rx="2" fill="#333"/>
      <path d="M30 30 q0 5 -9 5" fill="none" stroke="#333" stroke-width="2"/>
    </svg>
    <div>
      <div class="support-label">24/7 SALES SUPPORT</div>
      <div class="support-phone">0800-246-1357</div>
    </div>
  </div>
  <div class="abs lang">
    <svg width="28" height="16" viewBox="0 0 28 16" aria-hidden="true"><rect x="1" y="3" width="26" height="10" rx="5" fill="#4aa33a"/></svg>
    English<span class="lang-caret"></span>
  </div>
</header>

<section class="abs hero">
  <div class="hero-photo" role="img" aria-label="Photo of a turquoise bay with granite boulders and green hills"></div>
  <svg class="hero-curve" width="919" height="40" viewBox="0 0 919 40" aria-hidden="true">
    <path d="M0 0 H919 V40 Q460 -4 0 40 Z" fill="var(--blue)"/>
    <path d="M0 40 Q460 -4 919 40" fill="none" stroke="#2b7fb8" stroke-width="1.5" opacity=".6"/>
  </svg>
  <nav class="nav">
    <a style="width:83px">HOME</a>
    <a style="width:107px">DESTINATIONS</a>
    <a style="width:103px">ACTIVITIES</a>
    <a style="width:95px">TRIP STYLES</a>
    <a style="width:148px">RESPONSIBLE TRAVEL</a>
    <a style="width:73px">TOURS</a>
    <a style="width:91px">GALLERY</a>
    <a style="width:104px">ABOUT US</a>
    <a style="width:115px">CONTACT US</a>
  </nav>
  <h1 class="hero-title" style="font-weight:400">FIND A PLACE TO STAY</h1>
</section>

<section class="abs search">
  <div class="field" style="left:17px;top:20px;width:214px">Which Country you want to go?</div>
  <div class="field select" style="left:256px;top:20px;width:196px">In Which Region</div>
  <div class="field select" style="left:476px;top:20px;width:197px">Check In</div>
  <div class="field select" style="left:698px;top:20px;width:196px">Check Out</div>
  <div class="field select" style="left:17px;top:67px;width:136px">Range</div>
  <div class="field select" style="left:173px;top:67px;width:136px">Adults</div>
  <div class="field select" style="left:328px;top:67px;width:136px">Kids</div>
  <div class="field select" style="left:484px;top:67px;width:135px">Infants</div>
  <div class="checks">
    <div class="check"><span class="box"></span>Обратно</div>
    <div class="check"><span class="box"><svg width="9" height="9" viewBox="0 0 9 9" aria-hidden="true"><path d="M1 4.5 L3.5 7 L8 1.5" fill="none" stroke="#333" stroke-width="1.5"/></svg></span>В одну сторону</div>
  </div>
  <div class="proceed">PROCEED NOW</div>
</section>

<section>
  <div class="abs world-map" role="img" aria-label="Blue world map illustration"></div>
  <h2 class="abs welcome-title" style="font-weight:400">Welcome to Belvasco Travel</h2>
  <p class="abs welcome-text">Lorem Ipsum est simplement du faux texte employé dans la sition et la misen page avant impression. Le Lorem Ipsum est le faux texte standard de l'imprimerie depuis les années 1500, quand un peintre anonyme assembla ensemble des morceaux de texte pour réaliser un livre spécimen de polices de texte.</p>
</section>

<section>
  <h3 class="abs section-title" style="font-weight:400">Our Services</h3>
  <div class="abs section-rule"></div>
  <div class="card" style="left:125px">
    <div class="card-photo" role="img" aria-label="Beach parasol with two sun loungers by the sea" style="background:linear-gradient(180deg,#2f86c9 0%,#7cc0e4 50%,#3aa2c6 62%,#e6dccb 80%,#c9b79a 100%)"></div>
    <div class="card-label">Visa Services</div>
  </div>
  <div class="card active" style="left:350px">
    <div class="card-photo" role="img" aria-label="Wooden pier with a hut over dark teal water" style="background:linear-gradient(180deg,#1f4f5a 0%,#2a6a70 55%,#1d5a60 100%)"></div>
    <div class="card-label">Flight Services</div>
  </div>
  <div class="card" style="left:572px">
    <div class="card-photo" role="img" aria-label="Wooden deck chair facing a mountain lake" style="background:linear-gradient(180deg,#5aa0dc 0%,#c9dff0 25%,#6f8a7a 45%,#8fb7b0 65%,#b7693a 100%)"></div>
    <div class="card-label">Hotel Services</div>
  </div>
  <div class="card" style="left:795px">
    <div class="card-photo" role="img" aria-label="Thatched beach shelter on sand under a blue sky" style="background:linear-gradient(180deg,#3a86c8 0%,#a9cdea 45%,#d9cbb1 70%,#cdb793 100%)"></div>
    <div class="card-label">Other Services</div>
  </div>
</section>

<footer>
  <div class="abs footer">
    <div class="footer-notch"></div>
    <div class="footer-links"><span>Home</span><span>Destinations</span><span>Activities</span><span>Trip Styles</span><span>Responsible Travel</span></div>
    <div class="footer-rule" style="left:19px;width:655px"></div>
    <div class="footer-info" style="left:19px">
      <svg width="15" height="14" viewBox="0 0 15 14" aria-hidden="true"><path d="M1 7 L7.5 1 L14 7 M3 6 V13 H6 V9 H9 V13 H12 V6" fill="none" stroke="#8a8a8a" stroke-width="1.5"/></svg>
      <span>Lorem Ipsum is simply dummy text of the printinge</span>
    </div>
    <div class="footer-info" style="left:333px">
      <svg width="15" height="14" viewBox="0 0 15 14" aria-hidden="true"><path d="M3 1 L6 4 L4.5 6 Q6.5 9 9 10 L11 8.5 L14 11.5 L12 13.5 Q5 12 1.5 3 Z" fill="#8a8a8a"/></svg>
      <span>(123) 555-0148</span>
    </div>
    <div class="footer-info" style="left:454px">
      <svg width="15" height="11" viewBox="0 0 15 11" aria-hidden="true"><rect x=".75" y=".75" width="13.5" height="9.5" fill="none" stroke="#8a8a8a" stroke-width="1.5"/><path d="M1 1 L7.5 6 L14 1" fill="none" stroke="#8a8a8a" stroke-width="1.5"/></svg>
      <span>hello@belvascotravel.com</span>
    </div>
    <div class="stay">STAY CONNECTED</div>
    <div class="footer-rule" style="left:693px;width:206px"></div>
    <span class="social" style="left:700px"></span>
    <span class="social" style="left:733px"></span>
    <span class="social" style="left:766px"></span>
    <span class="social" style="left:799px"></span>
    <span class="social" style="left:832px"></span>
    <span class="social" style="left:865px"></span>
  </div>
  <div class="abs footer-bottom"><span>Belvasco Travel © 2013</span><span>Legal Notice</span><span>Terms</span></div>
</footer>
</body>
</html>
```